Web and Logo Design for eCommerce site

We're launching a sister brand and require a full design for the site.

The site must have an established feel and appeal to corporate and institutional buyers.
Updates

Just a note about the wireframe design:

The Search & Rescue / Coast Guard / NVDK, etc. in the header area aren't buttons or menu items, but rather just info (along the lines of a tagline).  Sort of a "who we serve" sort of thing.

Worth noting is that it's specifically geared towards LARGE BUYERS.  For example, a police force buying 200 headlamps and 85 pairs of gloves.  So they'll register + sign in and then add a bunch of items to a RFQ.

Aim for a professional, masculine design.

Target Market(s)

We will be selling outdoor gear to the military, law enforcement, fire and rescue and first responders.

Requirements
Must have
• We require:
- Logo (vector based)

Site:
- template page
* main site template, re-skinned version of our current site
* horizontal drop-down menu
- product listings page
* thumbnail view of products
- product details page
* including elements such as product image, color/size selector, descriptions and specs (again, based loosely on our current website)
- account management page
* illustrating basic data entry styles for text box, buttons, grid, etc.

The site needs to be given a responsive design, so 2 versions of each design should be presented for desktop + mobile views.

Additional funds are available if the designer is able to fully implement the designs into a responsive framework such as bootstrap.

Nice to have
• Clean, professional design similar to:

http://military.trailvexagear.com/gov/accessories/gloves.html

http://leaf.ombrivo.com/ProductFind.aspx?language=EN&category=Hardshell&subcat=Waterproof_Jackets

```html
<!DOCTYPE html>
<html lang="en">
<head>
<meta charset="utf-8">
<title>Ravelin – Canadian Outdoor Pro Supply</title>
<link href="https://fonts.googleapis.com/css2?family=Open+Sans:wght@400;600;700;800&display=swap" rel="stylesheet">
<style>
:root{
  --ink:#16120c;
  --gold:#c8901f;
  --gold-light:#d9a231;
  --navy:#0f1a2c;
  --text:#2b2b2b;
  --muted:#8d8d8d;
  --line:#e3e3e3;
  --panel:#f3f3f3;
  --footer:#1b1b1b;
  --footer-dark:#141414;
  --green:#8fa83a;
  --white:#ffffff;
}
*{box-sizing:border-box;margin:0;padding:0}
html,body{width:1200px;height:2198px;overflow:hidden}
body{font-family:"Open Sans",sans-serif;color:var(--text);background:var(--white);position:relative}
.abs{position:absolute}

.site-header{position:absolute;left:0;top:0;width:1200px;height:178px;background:var(--ink)}
.brand{position:absolute;left:112px;top:42px;display:flex;align-items:center;gap:12px}
.brand-mark{width:46px;height:46px;background:var(--gold)}
.brand-name{font-size:44px;font-weight:800;color:var(--white);letter-spacing:1px;line-height:1}
.cart{position:absolute;left:991px;top:0;width:98px;height:30px;background:var(--gold);color:var(--white);font-size:13px;font-weight:600;display:flex;align-items:center;justify-content:center;gap:8px}
.call{position:absolute;right:110px;top:70px;color:var(--white);font-size:20px}

.main-nav{position:absolute;left:110px;top:139px;width:980px;height:38px;background:linear-gradient(#d9a231,#b97f14);display:flex;align-items:center}
.main-nav a{color:var(--white);font-size:14px;text-decoration:none;padding:0 17px;border-right:1px solid rgba(255,255,255,.3);line-height:20px}
.main-nav a:last-child{border:none}
.main-nav a.active{font-weight:700}

.hero{position:absolute;left:0;top:177px;width:1200px;height:485px;background:linear-gradient(#f1f1f0,#ebe4d7)}
.serve{position:absolute;left:110px;top:0;width:980px;height:38px;background:var(--white);border:1px solid #ddd;display:flex;align-items:center;font-size:14px;color:#222}
.serve .label{background:#c9c9c9;height:30px;margin-left:4px;padding:0 8px;display:flex;align-items:center;font-weight:600;color:#333}
.serve span{margin-left:44px}
.hero-title{position:absolute;left:114px;top:122px;font-size:62px;font-weight:700;line-height:72px;color:var(--navy)}
.hero-title .gold{color:var(--gold)}
.read-more{position:absolute;left:120px;top:364px;width:114px;height:36px;background:var(--white);box-shadow:0 2px 3px rgba(0,0,0,.25);font-size:14px;font-weight:600;display:flex;align-items:center;justify-content:center;color:#222}
.dots{position:absolute;left:124px;top:447px;display:flex;gap:5px}
.dots i{width:12px;height:12px;border-radius:50%;background:var(--white);border:1px solid #bbb}
.dots i.on{background:#222;box-shadow:inset 0 0 0 3px #fff}
.hero-image{position:absolute;left:640px;top:56px;width:445px;height:400px;background:radial-gradient(ellipse at center,#8a7a58 0%,#6b6446 45%,rgba(235,228,215,0) 72%)}

.welcome{position:absolute;left:0;top:734px;width:1200px;text-align:center}
.welcome h1{font-size:26px;font-weight:400;color:#111}
.welcome h1 b{font-weight:700}
.welcome p{width:770px;margin:18px auto 0;font-size:13.5px;line-height:22px;color:#333}

.bar-title{position:absolute;top:935px;height:46px;background:var(--ink);border-bottom:3px solid var(--gold);color:var(--white);font-size:22px;font-weight:600;padding-left:10px;display:flex;align-items:center}
.cat-title{left:110px;width:238px}
.prod-title{left:356px;width:734px}
.arrows{position:absolute;right:10px;top:10px;width:70px;height:24px;background:var(--white);border-radius:12px;display:flex;align-items:center;justify-content:space-around}

.categories{position:absolute;left:110px;top:1003px;width:238px;list-style:none;border:1px solid var(--line)}
.categories li{height:40px;background:var(--panel);border-bottom:1px solid var(--line);font-size:13px;color:#333;padding-left:17px;display:flex;align-items:center}

.product{position:absolute;width:240px;height:403px;border:1px solid var(--line);background:var(--white)}
.product .photo{position:absolute;left:0;top:0;width:238px;height:285px;display:flex;align-items:center;justify-content:center}
.product .shape{width:130px;height:190px;border-radius:40px 40px 10px 10px}
.tan{background:linear-gradient(#b09a74,#8f7a56)}
.camo{background:linear-gradient(135deg,#a38f66,#7e7350 50%,#b7a27a)}
.product h3{position:absolute;left:0;top:303px;width:238px;text-align:center;font-size:16px;font-weight:600;line-height:20px;color:#111;border-top:1px solid var(--line);padding-top:16px;top:285px}
.product .price{position:absolute;left:-1px;bottom:-1px;width:240px;height:26px;background:var(--gold);color:var(--white);font-size:14px;display:flex;align-items:center;justify-content:center}
.sale{position:absolute;left:0;top:0;width:62px;height:20px;background:var(--gold);color:var(--white);font-size:13px;padding-left:6px;clip-path:polygon(0 0,100% 0,80% 100%,0 100%)}
.product.hover{background:#151515;border-color:#151515}
.product.hover h3{color:#3a3a3a;border-color:#151515}
.product.hover .price{background:#222;color:#333}
.product.hover .shape{background:#202020}
.hover-actions{position:absolute;left:66px;top:170px;display:flex;flex-direction:column;align-items:center;gap:4px}
.hover-actions .add{background:var(--gold);color:var(--white);font-size:12px;padding:2px 6px;font-weight:600}
.hover-actions .detail{border:1px solid var(--white);color:var(--white);font-size:14px;width:94px;text-align:center;line-height:20px}

.site-footer{position:absolute;left:0;top:1864px;width:1200px;height:286px;background:var(--footer)}
.foot-col{position:absolute;top:36px}
.foot-col h4{color:var(--white);font-size:14px;font-weight:600;padding-bottom:8px;border-bottom:1px solid #333;width:142px;margin-bottom:8px}
.foot-col li{list-style:none;color:var(--muted);font-size:13.5px;line-height:20px}
.signup{position:absolute;left:741px;top:38px;width:343px;height:214px;background:#242424;border-radius:3px;padding:8px 12px}
.signup h5{color:var(--white);font-size:14px;font-weight:600;padding:6px 0 8px;border-bottom:2px solid var(--gold);margin-bottom:10px}
.field{height:38px;background:var(--white);border:2px solid #ddd;position:relative;margin-bottom:34px}
.field b{position:absolute;right:4px;top:4px;height:26px;background:var(--green);color:var(--white);font-size:13px;font-weight:400;padding:0 16px;display:flex;align-items:center}
.copyright{position:absolute;left:0;top:2150px;width:1200px;height:48px;background:var(--footer-dark);color:#ddd;font-size:12.5px;display:flex;align-items:center;justify-content:center}
</style>
</head>
<body>
<header class="site-header">
  <div class="brand"><div class="brand-mark"></div><div class="brand-name">RAVELIN</div></div>
  <div class="cart">
    <svg width="14" height="14" viewBox="0 0 14 14"><rect x="1" y="4" width="12" height="9" fill="none" stroke="#fff" stroke-width="1.5"/><path d="M4 4V2.5a3 2 0 0 1 6 0V4" fill="none" stroke="#fff" stroke-width="1.5"/></svg>
    Cart (0)
  </div>
  <div class="call">Call: +123 (456) 7890</div>
</header>

<nav class="main-nav">
  <a class="active">RESCUE GEAR</a><a>FOOTWEAR</a><a>CLOTHING</a><a>TENTS MATS</a><a>SLEEPING BAGS</a><a>CAMPING GEAR</a><a>SNOW SPORTS</a><a>BRANDS</a>
</nav>

<section class="hero">
  <div class="serve"><span class="label" style="margin-left:4px">WHO WE SERVE:</span><span>Search &amp; Rescue</span><span>• Coast Guard</span><span>• NVDK</span><span>• Fire</span><span>• Mitary</span><span>• Law enforcement</span></div>
  <h2 class="hero-title"><span class="gold">CANADIAN</span><br>OUTDOOR<br>PRO SUPPLY</h2>
  <div class="read-more">READ MORE</div>
  <div class="dots"><i class="on"></i><i></i><i></i></div>
  <div class="hero-image" role="img" aria-label="Tactical helmet, camouflage backpack, combat boots and flashlight"></div>
</section>

<section class="welcome">
  <h1>WELCOME TO <b>OUR STORE</b></h1>
  <p>Lorem ipsum dolor sit amet, consectetur adipisicing elit, sed do eiusmod tempor incididunt ut labore et dolore magna aliqua. Ut enim ad minim veniam, quis nostrud exercitation ullamco laboris nisi ut aliquip ex ea commodo consequat. Duis aute irure dolor in reprehenderit in voluptate velit esse cillum dolore eu fugiat nulla pariatur. Excepteur sint occaecat cupidatat non proident, sunt in culpa qui officia deserunt mollit anim id est laborum.</p>
</section>

<div class="bar-title cat-title">CATEGORY</div>
<div class="bar-title prod-title">RAVELIN PRODUCT
  <div class="arrows"><svg width="10" height="10"><path d="M7 1L2 5l5 4z" fill="#111"/></svg><svg width="10" height="10"><path d="M3 1l5 4-5 4z" fill="#111"/></svg></div>
</div>

<ul class="categories">
  <li>Rescue Gear</li><li>Footwear</li><li>Clothing</li><li>T.ents Mats Sleeping Bags</li><li>Camping Gear</li><li>Snow Sports</li><li>Brands</li><li>Coast Guard</li><li>NVDK</li><li>Fire</li><li>Military</li><li>Law Enforcement</li><li>Lorem Ipsum Dolor</li><li>Sit Amet Consectetur</li><li>Adipisicing Elit, Sed Do</li><li>Eiusmod Tempor</li><li>Incididunt Ut Labore</li>
</ul>

<article class="product hover" style="left:356px;top:1003px">
  <div class="photo"><div class="shape" role="img" aria-label="Jacket photo"></div></div>
  <div class="hover-actions"><span class="add">ADD TO CART</span><span class="detail">DETAIL</span></div>
  <h3>RIDGE JACKET<br>TERRAPAT MEN'S GEN 2<br>REVISED</h3>
  <div class="price">$750.00 CAD</div>
</article>
<article class="product" style="left:602px;top:1003px">
  <div class="photo"><div class="shape tan" role="img" aria-label="Tan hardshell jacket photo"></div></div>
  <div class="sale">SALE</div>
  <h3>RIDGE JACKET<br>TERRAPAT MEN'S GEN 2<br>REVISED</h3>
  <div class="price">$750.00 CAD</div>
</article>
<article class="product" style="left:850px;top:1003px">
  <div class="photo"><div class="shape camo" role="img" aria-label="Camouflage jacket photo"></div></div>
  <h3>RIDGE JACKET<br>TERRAPAT MEN'S GEN 2<br>REVISED</h3>
  <div class="price">$750.00 CAD</div>
</article>
<article class="product" style="left:356px;top:1424px">
  <div class="photo"><div class="shape camo" role="img" aria-label="Camouflage hooded jacket photo"></div></div>
  <h3>RIDGE JACKET<br>TERRAPAT MEN'S GEN 2<br>REVISED</h3>
  <div class="price">$750.00 CAD</div>
</article>
<article class="product" style="left:602px;top:1424px">
  <div class="photo"><div class="shape tan" role="img" aria-label="Tan hardshell jacket photo"></div></div>
  <h3>RIDGE JACKET<br>TERRAPAT MEN'S GEN 2<br>REVISED</h3>
  <div class="price">$750.00 CAD</div>
</article>
<article class="product" style="left:850px;top:1424px">
  <div class="photo"><div class="shape camo" role="img" aria-label="Camouflage jacket photo"></div></div>
  <h3>RIDGE JACKET<br>TERRAPAT MEN'S GEN 2<br>REVISED</h3>
  <div class="price">$750.00 CAD</div>
</article>

<footer class="site-footer">
  <div class="foot-col" style="left:110px"><h4>NAVIGATION</h4><ul><li>Rescue Gear</li><li>Footwear</li><li>Clothing</li><li>Tents Mats</li><li>Sleeping Bags</li><li>Camping Gear</li><li>Snow Sports</li><li>Brands</li></ul></div>
  <div class="foot-col" style="left:315px"><h4>RAVELIN PRODUCT</h4><ul><li>Ridge Jacket</li><li>Ridge Jacket</li><li>Ridge Jacket</li><li>Ridge Jacket</li><li>Ridge Jacket</li><li>Ridge Jacket</li></ul></div>
  <div class="foot-col" style="left:531px"><h4>CONTACT US</h4><ul><li>Call: +123 (456) 7890</li><li>Fax: +123 (456) 7890</li><li>Address: Your Address</li><li>Here</li></ul></div>
  <div class="signup">
    <h5>EMAIL &amp; CATALOG SIGNUP</h5>
    <div class="field"><b>SIGN UP</b></div>
    <h5>FIND A RAVELIN</h5>
    <div class="field"><b>SEARCH</b></div>
  </div>
</footer>
<div class="copyright">© 2014 Ravelin - All Rights Reserved</div>
</body>
</html>
```